Trade Show Display Graphic Design Project

We are looking for a design of a trade show display and podium that is color coordinated with our logo and advertisements (attached).
We are a security consulting firm that provides 4 core services:
-Security Assessment and Planning
-Security Design and Engineering
-Managed Security Services
-Security Training
Our look should reflect a highly professional elite level of expertise.
BACKDROP
We are looking for a backdrop trade show display that is a spin off of the print advertisement we are doing in the trade show magazine (attached advertisement OVRA 2016 Ad.pdf). I am looking to emphasize our core services, possibly with an icon to represent each service and keep the "Identifying - Mitigating - Managing - The Threat" as part of the overall display as see in the print advertisement.
The side curved endcaps can be used to show the logo and name vertically but i will ask you to be creative in how you do the design.
The design should be sleek and simple.
PODIUM
The podium I see as our logo. possibly rearranged with the logo art on top and the text on bottom.
Attached are the technical design requirements for the backdrop and podium. Only follow the technical requirements of the documents. All artwork should be sent to me through the pixelbazaar website.
LINK TO IMAGE IN SUPPLIED PDF
https://www.filevaultly.net/s/0a9b6i5j19umr4h/Stockaro_42038944_XXL.jpg?dl=0
Target Market(s)
security directors and senior directors
Industry/Entity Type
Security
Other font styles liked:
- Match logo font
Requirements
Must have
- logo, core services

```html
<!DOCTYPE html>
<html lang="en">
<head>
<meta charset="utf-8">
<title>Corvane Advisory — Trade Show Backdrop</title>
<link rel="stylesheet" href="https://fonts.googleapis.com/css2?family=Open+Sans:ital,wght@0,700;1,300;1,400&display=swap">
<style>
  :root {
    --bg-deep: #0f0a09;
    --bg-mid: #2a211f;
    --bg-sheen: #6a5e5a;
    --seam: rgba(0, 0, 0, 0.55);
    --seam-light: rgba(255, 255, 255, 0.06);
    --brand-blue: #3a9ad9;
    --text-light: #f4f4f4;
    --text-soft: #d9d9d9;
  }
  html, body {
    margin: 0;
    padding: 0;
    overflow: hidden;
    background: var(--bg-deep);
  }
  .backdrop {
    position: relative;
    width: 1200px;
    height: 685px;
    overflow: hidden;
    background:
      repeating-linear-gradient(180deg, rgba(255,255,255,0.025) 0 2px, rgba(0,0,0,0.04) 2px 5px, rgba(255,255,255,0.015) 5px 9px),
      linear-gradient(180deg,
        #1b1413 0%,
        #3a302d 14%,
        var(--bg-sheen) 24%,
        #4a3f3b 31%,
        var(--bg-mid) 42%,
        #251c1a 55%,
        #1a1211 72%,
        var(--bg-deep) 100%);
    font-family: "Open Sans", Arial, sans-serif;
  }
  .sheen-arc {
    position: absolute;
    inset: 0;
  }
  .panel-seam {
    position: absolute;
    top: 0;
    width: 6px;
    height: 685px;
    background: linear-gradient(90deg, var(--seam), var(--seam-light), var(--seam));
  }
  .panel-seam--left { left: 423px; }
  .panel-seam--right { left: 771px; }
  .center-panel {
    position: absolute;
    left: 429px;
    top: 0;
    width: 342px;
    height: 685px;
    background: linear-gradient(90deg, rgba(255,255,255,0.03), rgba(255,255,255,0.06) 50%, rgba(255,255,255,0.03));
  }
  .brand {
    position: absolute;
    left: 429px;
    top: 96px;
    width: 342px;
    text-align: center;
  }
  .brand-dot {
    display: block;
    width: 72px;
    height: 72px;
    margin: 0 auto 24px;
    border-radius: 50%;
    background: var(--brand-blue);
  }
  .brand-name {
    margin: 0;
    font-size: 38px;
    font-weight: 700;
    line-height: 1.1;
    color: var(--text-light);
    letter-spacing: 0.5px;
  }
  .services {
    position: absolute;
    left: 452px;
    top: 344px;
    margin: 0;
    padding: 0;
    list-style: none;
  }
  .service {
    display: flex;
    align-items: center;
    height: 39px;
    font-size: 27px;
    font-style: italic;
    font-weight: 300;
    color: var(--text-soft);
  }
  .service-icon {
    width: 26px;
    height: 30px;
    margin-right: 10px;
    flex: none;
  }
</style>
</head>
<body>
<main class="backdrop">
  <svg class="sheen-arc" width="1200" height="685" viewBox="0 0 1200 685" aria-hidden="true">
    <path d="M0 150 Q600 250 1200 80" fill="none" stroke="rgba(255,255,255,0.12)" stroke-width="2"/>
    <path d="M0 150 Q600 250 1200 80 L1200 0 L0 0 Z" fill="rgba(0,0,0,0.18)"/>
  </svg>

  <div class="center-panel"></div>
  <div class="panel-seam panel-seam--left"></div>
  <div class="panel-seam panel-seam--right"></div>

  <header class="brand">
    <span class="brand-dot"></span>
    <h1 class="brand-name">Corvane Advisory</h1>
  </header>

  <ul class="services">
    <li class="service">
      <svg class="service-icon" viewBox="0 0 26 30" aria-hidden="true">
        <path d="M13 1 L25 5 V14 C25 22 19 27 13 29 C7 27 1 22 1 14 V5 Z" fill="var(--brand-blue)"/>
        <circle cx="13" cy="14" r="5" fill="none" stroke="#fff" stroke-width="2"/>
      </svg>Security Consulting
    </li>
    <li class="service">
      <svg class="service-icon" viewBox="0 0 26 30" aria-hidden="true">
        <path d="M13 1 L25 5 V14 C25 22 19 27 13 29 C7 27 1 22 1 14 V5 Z" fill="var(--brand-blue)"/>
        <circle cx="13" cy="11" r="3.5" fill="#fff"/>
        <rect x="11.5" y="13" width="3" height="7" fill="#fff"/>
      </svg>Security Engineering
    </li>
    <li class="service">
      <svg class="service-icon" viewBox="0 0 26 30" aria-hidden="true">
        <path d="M13 1 L25 5 V14 C25 22 19 27 13 29 C7 27 1 22 1 14 V5 Z" fill="var(--brand-blue)"/>
        <circle cx="13" cy="11" r="3.5" fill="#fff"/>
        <path d="M6.5 20 C7 16 19 16 19.5 20 Z" fill="#fff"/>
      </svg>Managed Security
    </li>
    <li class="service">
      <svg class="service-icon" viewBox="0 0 26 30" aria-hidden="true">
        <path d="M13 1 L25 5 V14 C25 22 19 27 13 29 C7 27 1 22 1 14 V5 Z" fill="var(--brand-blue)"/>
        <path d="M13 8 L14.8 12 L19 12.3 L15.8 15 L16.8 19.2 L13 17 L9.2 19.2 L10.2 15 L7 12.3 L11.2 12 Z" fill="#fff"/>
      </svg>Security Training
    </li>
  </ul>
</main>
</body>
</html>
```